Salon and Spa Distributor Business Card

Need a business card. We are are distributor in the salon and spa industry. We identify with natural beauty. Need a card with:
Company Name: Petal Quarry"
Title: "President & CEO"
Address
Company Phone number
email
website
Tag Line:" Natural Beauty, Pro Supplied"

Industry/Entity Type

Business

Contact Information for Business Card

Name: Dov Strommen
Title: "President & CEO"
Address: 31 Harlow Ln, Bexmoor, NJ 07813
Company Phone number: 800-463-5918
email: dovstrommen@petalquarry.example
website: www.petalquarry.example

Requirements
Should not have
• No black backgrounds

```html
<!DOCTYPE html>
<html lang="en">
<head>
<meta charset="utf-8">
<title>Petal Quarry — Business Card</title>
<link href="https://fonts.googleapis.com/css2?family=Source+Sans+3:wght@400;600;700&display=swap" rel="stylesheet">
<style>
  :root {
    --page-bg: #ecebe8;
    --card-white: #ffffff;
    --brand-green: #1e8a3c;
    --leaf-green: #4cae45;
    --deep-green: #13722f;
    --light-green: #5fba4a;
    --text-grey: #4a4a4a;
    --title-grey: #8a8a8a;
    --rule-grey: #d6d6d6;
  }
  * { margin: 0; padding: 0; box-sizing: border-box; }
  html, body {
    width: 1200px; height: 987px; overflow: hidden;
    background: var(--page-bg);
    font-family: "Source Sans 3", "Helvetica Neue", Arial, sans-serif;
  }
  .canvas { position: relative; width: 1200px; height: 987px; }
  .card {
    position: absolute; left: 293px; width: 615px; height: 351px;
    box-shadow: 0 2px 8px rgba(0,0,0,0.12);
  }
  .card-front { top: 130px; background: var(--card-white); }
  .card-back {
    top: 506px;
    background: radial-gradient(ellipse 62% 70% at 50% 40%, var(--light-green) 0%, var(--brand-green) 58%, var(--deep-green) 100%);
  }

  /* front: brand block */
  .front-brand {
    position: absolute; left: 44px; top: 136px;
    display: flex; align-items: center; gap: 12px;
  }
  .brand-dot {
    width: 80px; height: 80px; border-radius: 50%;
    background: var(--leaf-green);
    flex: none;
  }
  .front-brand-name {
    font-size: 24px; font-weight: 400; color: var(--leaf-green); white-space: nowrap;
  }
  .divider {
    position: absolute; left: 305px; top: 87px;
    width: 1px; height: 187px; background: var(--rule-grey);
  }

  /* front: contact block */
  .contact { position: absolute; left: 326px; top: 84px; color: var(--text-grey); }
  .contact-company { font-size: 23px; font-weight: 700; color: var(--brand-green); line-height: 1.1; }
  .contact-title { font-size: 16px; color: var(--title-grey); margin-top: 2px; }
  .contact-address { font-size: 16px; line-height: 22px; margin-top: 8px; }
  .contact-list { list-style: none; margin-top: 4px; font-size: 16px; }
  .contact-list li { display: flex; align-items: center; gap: 8px; height: 23.5px; white-space: nowrap; }
  .contact-list svg { width: 13px; height: 13px; fill: var(--brand-green); flex: none; }

  /* back */
  .back-brand {
    position: absolute; left: 98px; top: 116px;
    display: flex; align-items: center; gap: 16px;
  }
  .back-dot {
    width: 140px; height: 140px; border-radius: 50%;
    background: rgba(255,255,255,0.9);
    flex: none;
  }
  .back-text { padding-top: 26px; }
  .back-brand-name { font-size: 40px; font-weight: 400; color: #fff; line-height: 1; white-space: nowrap; }
  .back-tagline { font-size: 17px; font-weight: 600; color: #fff; margin-top: 8px; padding-left: 4px; white-space: nowrap; }
</style>
</head>
<body>
<main class="canvas">
  <section class="card card-front" aria-label="Card front">
    <div class="front-brand">
      <span class="brand-dot"></span>
      <span class="front-brand-name">Petal Quarry</span>
    </div>
    <div class="divider"></div>
    <div class="contact">
      <p class="contact-company">Petal Quarry</p>
      <p class="contact-title">President &amp; CEO</p>
      <p class="contact-address">31 Harlow Ln<br>Bexmoor, NJ 07813</p>
      <ul class="contact-list">
        <li>
          <svg viewBox="0 0 24 24" aria-hidden="true"><path d="M6.6 10.8a15.1 15.1 0 0 0 6.6 6.6l2.2-2.2a1 1 0 0 1 1-.25 11.4 11.4 0 0 0 3.6.57 1 1 0 0 1 1 1V20a1 1 0 0 1-1 1A17 17 0 0 1 3 4a1 1 0 0 1 1-1h3.5a1 1 0 0 1 1 1c0 1.25.2 2.45.57 3.57a1 1 0 0 1-.25 1z"/></svg>
          800-463-5918
        </li>
        <li>
          <svg viewBox="0 0 24 24" aria-hidden="true"><path d="M2 5h20l-10 7.5z"/><path d="M2 6.5V19h20V6.5l-10 7.5z"/></svg>
          dovstrommen@petalquarry.example
        </li>
        <li>
          <svg viewBox="0 0 24 24" aria-hidden="true"><circle cx="12" cy="12" r="10"/><path d="M2 12h20M12 2c3 3 3 17 0 20M12 2c-3 3-3 17 0 20" fill="none" stroke="#fff" stroke-width="1.5"/></svg>
          www.petalquarry.example
        </li>
      </ul>
    </div>
  </section>

  <section class="card card-back" aria-label="Card back">
    <div class="back-brand">
      <span class="back-dot"></span>
      <div class="back-text">
        <p class="back-brand-name">Petal Quarry</p>
        <p class="back-tagline">Natural Beauty, Pro Supplied</p>
      </div>
    </div>
  </section>
</main>
</body>
</html>
```